Lantern Petals Website v.1 - attract floral shop franchisees

I need a simple information website for my new business. We are a franchisor of flower shops. The overall purpose of the website is to promote the company and the service, especially to potential franchisees and retailers. Only about 4 pages are required including homepage, About, For Supermarkets, For Franchisees, and Contact. No special functions are required except the site will have two separate inquiry forms that must be filled out online and submitted via automated email. Similarly, an email form should be linked from the Contact page. I have a logo and business cards designed by ArtMingle, and I would like the site to have a consistent color scheme and style. The key to design will be to express the joy and love associated with flowers and floral bouquets.
IMPORTANT - I will be exporting the website design to Wordpress CMS in a site hosted by HostNimbus. For smooth integration into WordPress hosted by HostNimbus, the designer should build the site using a WordPress-friendly format. Ideally, they should use HTML, CSS, and PHP. Creating a custom theme or using a page builder that exports to WordPress-compatible files is best. This ensures the site can be easily imported and managed within WordPress.

Target Market(s)

Potential franchisees (existing florists or creative types who might like to own a floral business) and supermarkets who might want us to run their floral department

Industry/Entity Type

Floral retailing

Requirements
Must have
• A brand theme that is beautiful, consistent throughout and builds on the logo design
Nice to have
• Show gender and ethnic diversity in customers and florists. Pictures of happy florists (for franchisees) and pictures of amazing floral department displays (for supermarkets)

```html
<!DOCTYPE html>
<html lang="en">
<head>
<meta charset="utf-8">
<title>Lantern Petals – Floral Franchising</title>
<link href="https://fonts.googleapis.com/css2?family=Poppins:wght@400;500;600;700&family=Great+Vibes&display=swap" rel="stylesheet">
<style>
:root{
  --orange:#f39200;
  --green:#138a36;
  --ink:#1e1e1e;
  --text:#3a3a3a;
  --grey-band:#efefef;
  --cream:#fdf5e6;
  --white:#ffffff;
  --rose:#d9467a;
  --rose-soft:#ef9db8;
  --leaf:#4d7a3e;
  --leaf-dark:#2f4d2a;
  --hydrangea:#eef0e0;
  --sun:#e8b53a;
  --wood:#7a5236;
}
*{margin:0;padding:0;box-sizing:border-box}
html,body{width:1200px;height:3384px;overflow:hidden}
body{position:relative;background:var(--white);font-family:'Poppins',sans-serif;color:var(--text)}
.abs{position:absolute}

/* hero */
.hero{left:0;top:0;width:1200px;height:640px;background:linear-gradient(135deg,#eaf3f6 0%,#f8fbfc 45%,#f1f6f8 70%,#fdf1eb 100%);border-bottom:1px solid #e6ead9}
.hero-bloom-pink{left:0;top:90px;width:150px;height:170px;border-radius:50%;background:radial-gradient(circle,#e9558a 0%,#f49ab9 50%,rgba(249,200,220,0) 74%)}
.hero-bloom-peach{left:1020px;top:470px;width:180px;height:170px;border-radius:50% 0 0 0;background:radial-gradient(circle at 60% 60%,#f58d72 0%,#fbc2a9 52%,rgba(253,230,220,0) 80%)}
.brand{left:142px;top:40px;display:flex;align-items:center;gap:12px}
.brand-dot{width:44px;height:44px;border-radius:50%;background:var(--orange);flex:none}
.brand-name{font-size:32px;font-weight:600;color:var(--orange);white-space:nowrap}
.nav a{position:absolute;top:56px;font-size:13px;color:var(--ink);text-decoration:none;white-space:nowrap}
.nav a.active{color:var(--orange);border-bottom:1px solid var(--orange);padding-bottom:2px}
.hero-title{left:139px;top:200px;width:520px;font-size:38px;line-height:42px;font-weight:700;color:var(--ink)}
.hero-copy{left:142px;top:342px;width:470px;font-size:11.5px;line-height:19px;color:var(--ink)}
.btn{left:141px;top:425px;width:142px;height:35px;border-radius:18px;background:var(--orange);color:#fff;font-size:12px;display:flex;align-items:center;padding-left:15px}
.btn::after{content:"";position:absolute;right:4px;top:4px;width:27px;height:27px;border-radius:50%;background:#fff}

.bouquet-a{background:radial-gradient(circle at 35% 30%,var(--hydrangea) 0 18%,rgba(238,240,224,0) 34%),radial-gradient(circle at 70% 45%,var(--rose) 0 14%,rgba(217,70,122,0) 30%),radial-gradient(circle at 30% 75%,var(--leaf) 0 20%,rgba(77,122,62,0) 42%),linear-gradient(160deg,#b9bcb0,#7f9a6c 55%,#3f5e34)}
.bouquet-b{background:radial-gradient(circle at 60% 40%,var(--rose) 0 16%,rgba(217,70,122,0) 34%),radial-gradient(circle at 30% 70%,#c9a07a 0 14%,rgba(201,160,122,0) 32%),linear-gradient(160deg,var(--leaf-dark),var(--leaf) 50%,#6a4530)}
.bouquet-c{background:radial-gradient(circle at 40% 55%,var(--rose) 0 16%,rgba(217,70,122,0) 34%),radial-gradient(circle at 65% 30%,var(--hydrangea) 0 18%,rgba(238,240,224,0) 36%),linear-gradient(160deg,#b34248,#e07a9c 50%,#dfe3d2)}
.bouquet-d{background:radial-gradient(circle at 35% 40%,#f07aa4 0 20%,rgba(240,122,164,0) 40%),radial-gradient(circle at 70% 70%,#c4285e 0 18%,rgba(196,40,94,0) 38%),linear-gradient(160deg,#e4548a,#b92b5a)}
.petal-tl{left:628px;top:149px;width:143px;height:169px;border-radius:72px 72px 0 72px}
.petal-bl{left:628px;top:331px;width:143px;height:142px;border-radius:72px 0 72px 72px}
.petal-tr{left:916px;top:149px;width:143px;height:169px;border-radius:72px 72px 72px 0}
.petal-br{left:916px;top:331px;width:143px;height:142px;border-radius:0 72px 72px 72px}
.petal-c{left:783px;top:131px;width:121px;height:384px}

/* about */
.ap-main{left:143px;top:782px;width:245px;height:315px;border-radius:122px 0 0 122px;background:radial-gradient(ellipse at 55% 78%,#f4f1e4 0 14%,rgba(244,241,228,0) 30%),radial-gradient(circle at 40% 55%,var(--sun) 0 14%,rgba(232,181,58,0) 30%),radial-gradient(circle at 20% 55%,#e37a3a 0 10%,rgba(227,122,58,0) 24%),linear-gradient(180deg,#b9c4b6,#8d9a90 50%,#4a3a2e)}
.ap-top{left:410px;top:732px;width:175px;height:222px;border-radius:40px 0 88px 0;background:radial-gradient(circle at 40% 45%,#e87a2c 0 16%,rgba(232,122,44,0) 34%),radial-gradient(circle at 70% 35%,var(--sun) 0 14%,rgba(232,181,58,0) 32%),linear-gradient(160deg,#6e6a5c,#a46a34 50%,#3a3a36)}
.ap-bot{left:410px;top:975px;width:175px;height:222px;border-radius:88px 0 0 88px;background:radial-gradient(circle at 40% 40%,#e0508a 0 16%,rgba(224,80,138,0) 34%),radial-gradient(circle at 70% 60%,var(--leaf) 0 18%,rgba(77,122,62,0) 38%),linear-gradient(170deg,#6c4a32,#a9566e 45%,#7a4a2e)}
.script{font-family:'Great Vibes',cursive;color:var(--ink);font-weight:400}
.script span{color:var(--orange)}
.about-title{left:651px;top:744px;font-size:56px;line-height:60px}
.divider{display:flex;align-items:center;gap:8px}
.divider i{display:block;width:40px;height:2px;background:var(--green)}
.divider b{display:block;width:14px;height:14px;border-radius:50%;background:var(--green)}
.about-div{left:651px;top:812px}
.about-copy{left:651px;top:853px;width:405px;font-size:11.2px;line-height:23px}
.about-copy p+p{margin-top:8px}
.sketch{background:radial-gradient(ellipse,#d3dbe0 0%,rgba(230,236,240,0) 70%)}
.sketch-about{left:985px;top:985px;width:215px;height:285px}

/* story band */
.story{left:0;top:1281px;width:1200px;height:460px;background:var(--grey-band)}
.story-copy{left:141px;top:1393px;width:445px;font-size:11.2px;line-height:23px}
.story-copy p+p{margin-top:7px}
.sketch-story{left:15px;top:1590px;width:110px;height:140px}
.arch{left:668px;top:1354px;width:383px;height:486px;border-radius:192px 192px 0 0;background:#fff;box-shadow:0 4px 14px rgba(0,0,0,.06)}
.arch-photo{left:678px;top:1367px;width:363px;height:460px;border-radius:182px 182px 0 0;background:radial-gradient(ellipse at 65% 45%,#c9ccd2 0 16%,rgba(201,204,210,0) 34%),radial-gradient(circle at 25% 40%,#d9708f 0 10%,rgba(217,112,143,0) 24%),radial-gradient(circle at 20% 55%,var(--leaf) 0 14%,rgba(77,122,62,0) 30%),linear-gradient(180deg,#3c3a33,#6e6050 45%,#8b5a38 80%,#5a3a26)}
.round-btn{width:46px;height:46px;border-radius:50%;display:flex;align-items:center;justify-content:center}
.round-btn.outline{border:2px solid var(--green);background:#fff}
.round-btn.solid{background:var(--green)}

/* gallery */
.gallery-bg{left:0;top:2113px;width:1200px;height:401px;background:radial-gradient(circle at 10% 20%,rgba(168,40,50,.55) 0 3%,rgba(168,40,50,0) 6%),radial-gradient(circle at 80% 30%,rgba(168,40,50,.5) 0 3%,rgba(168,40,50,0) 6%),radial-gradient(circle at 45% 85%,rgba(168,40,50,.5) 0 3%,rgba(168,40,50,0) 6%),radial-gradient(ellipse at 60% 45%,rgba(40,70,120,.5) 0 10%,rgba(40,70,120,0) 25%),linear-gradient(180deg,#22261f,#2a3326 45%,#2a2620 75%,#1f241c)}
.card{border:3px solid #fff}
.g1{left:142px;top:1913px;width:213px;height:271px;border-radius:0 0 70px 0;background:radial-gradient(circle at 65% 40%,var(--hydrangea) 0 16%,rgba(238,240,224,0) 32%),radial-gradient(circle at 35% 65%,#c2345e 0 18%,rgba(194,52,94,0) 36%),linear-gradient(170deg,#a9aaa6,#7d8a6e 55%,#4a3a2a)}
.g2{left:377px;top:1942px;width:212px;height:271px;border-radius:70px 0 70px 0;background:radial-gradient(circle at 75% 75%,#d8344a 0 14%,rgba(216,52,74,0) 30%),radial-gradient(circle at 30% 80%,#e6a0b4 0 14%,rgba(230,160,180,0) 30%),radial-gradient(circle at 70% 30%,#6a8a9a 0 10%,rgba(106,138,154,0) 24%),linear-gradient(170deg,#ece2dc,#c8b4aa 50%,#7a8a4a)}
.g3{left:611px;top:1913px;width:213px;height:271px;border-radius:0 0 70px 0;background:radial-gradient(ellipse at 50% 40%,#5a4a3e 0 14%,rgba(90,74,62,0) 30%),radial-gradient(circle at 30% 80%,#e0a8b8 0 14%,rgba(224,168,184,0) 30%),linear-gradient(170deg,#6a7356,#b49aa0 50%,#8aa37c)}
.g4{left:845px;top:1942px;width:214px;height:271px;border-radius:70px 70px 0 0;background:radial-gradient(circle at 50% 45%,#9a2a3a 0 14%,rgba(154,42,58,0) 30%),radial-gradient(ellipse at 50% 85%,#f4ece6 0 20%,rgba(244,236,230,0) 40%),radial-gradient(circle at 25% 80%,#c22a3a 0 10%,rgba(194,42,58,0) 22%),linear-gradient(170deg,#e6e2dc,#d8d0c8 60%,#c9b8b0)}
.partner{left:0;top:2314px;width:1200px;text-align:center;color:#fff;font-size:15px;font-weight:600;letter-spacing:6px}
.partner-copy{left:160px;top:2393px;width:880px;text-align:center;color:#fff;font-size:11.2px;line-height:23px}

/* testimonials */
.t-title{left:0;top:2586px;width:1200px;text-align:center;font-size:56px;line-height:60px}
.t-div{left:538px;top:2654px}
.t-card{left:217px;top:2736px;width:766px;height:211px;border-radius:24px;background:var(--cream)}
.avatar{left:564px;top:2699px;width:70px;height:70px;border-radius:50%;background:linear-gradient(160deg,#8a5a44,#c98a6a 50%,#4aa0c8);border:3px solid #fff}
.t-name{left:0;top:2796px;width:1200px;text-align:center;font-size:26px}
.t-quote{left:355px;top:2842px;width:490px;text-align:center;font-size:11.6px;line-height:23px;color:var(--ink)}
.stars{left:0;top:2902px;width:1200px;text-align:center;color:var(--orange);font-size:14px;letter-spacing:3px}
.sketch-t1{left:238px;top:2790px;width:96px;height:130px;background:radial-gradient(ellipse,#aeb6c4 0%,rgba(253,245,230,0) 70%)}
.sketch-t2{left:858px;top:2780px;width:110px;height:150px;background:radial-gradient(ellipse,#aeb6c4 0%,rgba(253,245,230,0) 70%)}

/* footer */
.footer{left:0;top:3032px;width:1200px;height:352px;background:var(--green)}
.f-head{font-family:'Great Vibes',cursive;color:#fff;font-size:24px}
.f-div{display:flex;align-items:center;gap:6px}
.f-div i{display:block;width:20px;height:1px;background:#fff}
.f-div b{display:block;width:9px;height:9px;border-radius:50%;background:#fff}
.f-links a{position:absolute;left:141px;color:#fff;font-size:12px;text-decoration:none;white-space:nowrap}
.f-brand{left:411px;top:3130px;display:flex;align-items:center;gap:12px}
.f-brand .brand-dot{width:46px;height:46px}
.social{left:483px;top:3245px;display:flex;gap:7px}
.social span{display:block;width:28px;height:28px;border-radius:50%;border:1.5px solid #fff}
.c-item{left:853px;display:flex;align-items:center;gap:14px;color:#fff;font-size:12px;line-height:18px;white-space:nowrap}
.c-icon{width:36px;height:36px;border-radius:50%;background:var(--orange);display:flex;align-items:center;justify-content:center;flex:none}
.f-rule{left:141px;top:3345px;width:918px;height:1px;background:rgba(255,255,255,.25)}
.copyright{left:0;top:3356px;width:1200px;text-align:center;color:#fff;font-size:12px}
</style>
</head>
<body>

<section class="abs hero" aria-label="Hero"></section>
<div class="abs hero-bloom-pink" role="img" aria-label="Painted pink flowers"></div>
<div class="abs hero-bloom-peach" role="img" aria-label="Painted peach dahlias"></div>

<div class="abs brand"><span class="brand-dot"></span><span class="brand-name">Lantern Petals</span></div>
<nav class="nav">
  <a class="active" style="left:615px" href="#">About Us</a>
  <a style="left:711px" href="#">For Supermakets</a>
  <a style="left:857px" href="#">For Franchisees</a>
  <a style="left:994px" href="#">Contact Us</a>
</nav>

<h1 class="abs hero-title">Flowers Expressed Feelings Of Surprise, Happiness and gratitude.</h1>
<p class="abs hero-copy">Get franchisor of flower shops. Nibh euismod tincidunt ut laoreet dolore magna aliquam erat volutpat. Ut wisi enim ad minim veniam.</p>
<div class="abs btn">Get Franchisee</div>

<div class="abs bouquet-a petal-tl" role="img" aria-label="Bouquet of white hydrangeas and pink roses"></div>
<div class="abs bouquet-b petal-bl" role="img" aria-label="Roses with green foliage"></div>
<div class="abs bouquet-c petal-tr" role="img" aria-label="Pink roses and hydrangeas"></div>
<div class="abs bouquet-d petal-br" role="img" aria-label="Bunch of pink roses"></div>
<svg class="abs petal-c" viewBox="0 0 121 384" role="img" aria-label="Tall arrangement of roses and hydrangeas">
  <defs><linearGradient id="centreFill" x1="0" y1="0" x2="0" y2="1">
    <stop offset="0" stop-color="#c9c4b0"/><stop offset=".3" stop-color="#e8ead8"/><stop offset=".55" stop-color="#d9507f"/><stop offset=".8" stop-color="#4d7a3e"/><stop offset="1" stop-color="#2f4d2a"/>
  </linearGradient></defs>
  <path d="M0 60 A60 60 0 0 1 121 60 V340 Q90 352 60 384 Q31 352 0 340 Z" fill="url(#centreFill)"/>
</svg>

<div class="abs ap-main" role="img" aria-label="Founder holding colourful bouquets in a flower workshop"></div>
<div class="abs ap-top" role="img" aria-label="Arrangement of orange protea and yellow flowers"></div>
<div class="abs ap-bot" role="img" aria-label="Vases of mixed pink flowers on a counter"></div>

<h2 class="abs script about-title">About <span>Us</span></h2>
<div class="abs divider about-div"><i></i><b></b><i></i></div>
<div class="abs about-copy">
  <p>Fresh flowers convey beauty and love, and in our view should become something every person regularly enjoys.  Lantern Petals is an entrepreneurial company created to make top quality fresh flowers and professionally-designed bouquets accessible to every consumer at affordable prices.</p>
  <p>Professional florists typically sell the finest quality stems, design the most beautiful bouquets and provide the finest customer service, but their costs – of floral products, retail spaces, labor and marketing – force them to pass high prices along to customers. Supermarket flower departments benefit from high customer footfall, economies of scale and low pricing, but their quality of stems and bouquets is typically poor, staffing is limited, and staff turnover is high which can result in inefficiency, wastage, poorly merchandised selections and limited service.</p>
</div>
<div class="abs sketch sketch-about" role="img" aria-label="Line drawing of lilies"></div>

<section class="abs story" aria-label="Our model"></section>
<div class="abs story-copy">
  <p>Lantern Petals brings the best of professional florists and supermarkets together for the benefit of consumers.  It supports a national network of owner-operator franchisees, who in many cases are multi-site professional florists, with comprehensive services to enhance franchise profitability.  Lantern Petals works with some of the country's largest and most progressive supermarkets to provide franchisee ownership and operation of their strategically important floral departments.</p>
  <p>Supermarkets find that Lantern Petals is able to improve their financial outcomes, provide attentive customer service and satisfaction, and lift the quality of the entire store environment.</p>
</div>
<div class="abs sketch sketch-story" role="img" aria-label="Line drawing of small flowers"></div>
<div class="abs arch"></div>
<div class="abs arch-photo" role="img" aria-label="Florist arranging roses at a wooden table"></div>
<div class="abs round-btn outline" style="left:541px;top:1762px">
  <svg width="12" height="12" viewBox="0 0 12 12"><path d="M8 2 4 6l4 4" fill="none" stroke="#1e1e1e" stroke-width="2"/></svg>
</div>
<div class="abs round-btn solid" style="left:602px;top:1762px">
  <svg width="12" height="12" viewBox="0 0 12 12"><path d="M4 2l4 4-4 4" fill="none" stroke="#fff" stroke-width="2"/></svg>
</div>

<div class="abs gallery-bg" role="img" aria-label="Field of red gerbera flowers in a greenhouse"></div>
<div class="abs card g1" role="img" aria-label="Large mixed bouquet of roses and hydrangeas"></div>
<div class="abs card g2" role="img" aria-label="Florist arranging flowers in buckets"></div>
<div class="abs card g3" role="img" aria-label="Flower shop storefront full of blooms"></div>
<div class="abs card g4" role="img" aria-label="Smiling florist in an apron behind flowers"></div>
<div class="abs partner">NORTHGALE GROUP</div>
<p class="abs partner-copy">Lantern Petals operates in partnership with Northgale Group, the leading franchisor of sushi stations and pre-packaged fruit &amp; vegetable departments to supermarkets across the United States and United Kingdom.  Lantern Petals' combination of floral and supermarket franchising expertise guarantees that consumers, franchisees and supermarket partners each receive exceptional service and value.</p>

<h2 class="abs script t-title">What Our Customers <span>Say</span></h2>
<div class="abs divider t-div"><i></i><b></b><i></i></div>
<div class="abs t-card"></div>
<div class="abs avatar" role="img" aria-label="Customer portrait"></div>
<div class="abs sketch-t1" role="img" aria-label="Line drawing of a flowering sprig"></div>
<div class="abs sketch-t2" role="img" aria-label="Line drawing of a leafy branch"></div>
<p class="abs script t-name">Mara <span>Ellison</span></p>
<p class="abs t-quote">Lorem ipsum dolor sit amet, consectetur adipiscing elit, sed do eiusmod tempor incididunt ut labore et dolore magna aliqua.</p>
<p class="abs stars">★★★★★</p>
<div class="abs round-btn outline" style="left:157px;top:2824px;width:36px;height:36px">
  <svg width="10" height="10" viewBox="0 0 12 12"><path d="M8 2 4 6l4 4" fill="none" stroke="#1e1e1e" stroke-width="2"/></svg>
</div>
<div class="abs round-btn solid" style="left:1007px;top:2824px;width:36px;height:36px">
  <svg width="10" height="10" viewBox="0 0 12 12"><path d="M4 2l4 4-4 4" fill="none" stroke="#fff" stroke-width="2"/></svg>
</div>

<footer class="abs footer"></footer>
<p class="abs f-head" style="left:141px;top:3086px">Quick Links</p>
<div class="abs f-div" style="left:141px;top:3117px"><i></i><b></b><i></i></div>
<div class="f-links">
  <a style="top:3142px" href="#">Home</a>
  <a style="top:3175px" href="#">About Us</a>
  <a style="top:3208px" href="#">For Supermarkets</a>
  <a style="top:3241px" href="#">For Franchisees</a>
  <a style="top:3275px" href="#">Contact Us</a>
</div>

<div class="abs f-brand"><span class="brand-dot"></span><span class="brand-name">Lantern Petals</span></div>
<div class="abs social" aria-label="Social links"><span></span><span></span><span></span><span></span></div>

<p class="abs f-head" style="left:853px;top:3086px">Contact Details</p>
<div class="abs f-div" style="left:853px;top:3117px"><i></i><b></b><i></i></div>
<div class="abs c-item" style="top:3148px">
  <span class="c-icon"><svg width="14" height="18" viewBox="0 0 14 18"><path d="M7 0a7 7 0 0 0-7 7c0 5 7 11 7 11s7-6 7-11a7 7 0 0 0-7-7z" fill="#fff"/><circle cx="7" cy="7" r="2.5" fill="#f39200"/></svg></span>
  <span>48 Meadow Lane, Suite 2<br>Brookfield, ST 00417</span>
</div>
<div class="abs c-item" style="top:3199px">
  <span class="c-icon"><svg width="16" height="16" viewBox="0 0 24 24"><path d="M6.6 10.8a15 15 0 0 0 6.6 6.6l2.2-2.2a1 1 0 0 1 1-.25 11.4 11.4 0 0 0 3.6.57 1 1 0 0 1 1 1V20a1 1 0 0 1-1 1A17 17 0 0 1 3 4a1 1 0 0 1 1-1h3.5a1 1 0 0 1 1 1c0 1.25.2 2.45.57 3.6a1 1 0 0 1-.25 1z" fill="#fff"/></svg></span>
  <span>555-014-2288</span>
</div>
<div class="abs c-item" style="top:3250px">
  <span class="c-icon"><svg width="16" height="12" viewBox="0 0 16 12"><rect width="16" height="12" rx="1.5" fill="#fff"/><path d="M1 1l7 6 7-6" fill="none" stroke="#f39200" stroke-width="1.5"/></svg></span>
  <span>info@lanternpetals.com</span>
</div>
<div class="abs f-rule"></div>
<p class="abs copyright">©2024 Lantern Petals. All Rights Reserved.</p>

</body>
</html>
```